Professional Package for CPA Firm

We would like a stationery design for our new CPA Firm based in Atlanta, GA called 'Vale 8'. We work with investors to help grow investments, tax free. We would like the design to have a professional/minimal look with a 'wow' factor. We need 9.5″ x 4.125″, 9x12, and 10x13 mailing envelopes, business cards, and a letterhead. We have a logo that is already complete. For the letterhead, we would like to have space to put credentials at the bottom of the page

Industry/Entity Type

CPA, Accounting

```html
<!DOCTYPE html>
<html lang="en">
<head>
<meta charset="utf-8">
<title>Vale 8 Stationery</title>
<link href="https://fonts.googleapis.com/css2?family=Montserrat:wght@500;700;800&family=Roboto:wght@400;500;700&display=swap" rel="stylesheet">
<style>
:root{
  --blue:#2b9ad6;
  --ink:#1c1c1e;
  --black:#161616;
  --paper:#ffffff;
  --grey-text:#555a60;
  --stage-dark:#2c2c2c;
  --stage-light:#e4e5e7;
  --wordmark-light:#d9d9d9;
}
*{box-sizing:border-box;margin:0;padding:0}
html,body{width:1200px;height:3488px;overflow:hidden}
body{font-family:"Roboto",sans-serif;color:var(--ink);background:var(--stage-light)}
.stage{position:relative;width:1200px}
.stage--cards{height:900px;background:radial-gradient(circle at 50% 30%,#3a3a3a,var(--stage-dark))}
.stage--letter{height:792px;background:var(--stage-light)}
.stage--envelopes{height:785px;background:var(--stage-light)}
.stage--large{height:1011px;background:linear-gradient(#e9eaec,#d9dadc)}
.piece{position:absolute;background:var(--paper);box-shadow:0 8px 24px rgba(0,0,0,.18)}
.wordmark{display:inline-flex;align-items:center;gap:8px;font-family:"Montserrat",sans-serif;font-weight:800;color:var(--ink);letter-spacing:.02em;line-height:1}
.wordmark__square{display:inline-block;background:var(--blue)}
.wordmark--light{color:var(--wordmark-light)}
/* business card front */
.card{width:520px;height:297px}
.card--front{left:60px;top:320px;display:flex;align-items:center;padding:0 36px}
.card--front .wordmark{font-size:40px}
.card--front .wordmark__square{width:14px;height:14px}
.card__divider{width:2px;height:150px;background:var(--ink);margin:0 28px}
.card__name{font-family:"Montserrat",sans-serif;font-weight:700;font-size:17px;text-transform:uppercase}
.card__role{font-family:"Montserrat",sans-serif;font-weight:500;color:var(--blue);font-size:14px;margin:2px 0 14px}
.contact{list-style:none;font-size:12.5px;color:var(--grey-text);line-height:1.55}
.contact li{display:flex;align-items:flex-start;gap:7px}
.contact svg{width:11px;height:11px;margin-top:4px;flex:none;fill:var(--ink)}
.card--back{left:620px;top:160px;background:var(--black);display:flex;align-items:center;justify-content:center}
.card--back .wordmark{font-size:48px}
.card--back .wordmark__square{width:16px;height:16px}
/* letterhead */
.letterhead{padding:36px 34px}
.letterhead__head{display:flex;justify-content:space-between;align-items:flex-start}
.letterhead__head .wordmark{font-size:20px}
.letterhead__head .wordmark__square{width:8px;height:8px}
.letterhead__firm{font-size:7.5px;line-height:1.45;color:var(--grey-text)}
.letterhead__firm strong{color:var(--blue);font-weight:500;display:block}
.letterhead__contact{font-size:7px;color:var(--grey-text);margin-top:4px;list-style:none;line-height:1.5}
.letterhead__body{margin-top:40px;font-size:7.5px;line-height:1.6;color:var(--grey-text)}
.letterhead__body p{margin-bottom:9px}
.letterhead--small{left:200px;top:80px;width:440px;height:622px}
.letterhead--tall{left:510px;top:300px;width:420px;height:600px;padding:46px 40px}
.letterhead--tall .wordmark{font-size:26px}
.letterhead--tall .wordmark__square{width:10px;height:10px}
.letterhead__foot{position:absolute;left:40px;bottom:40px;font-size:8.5px;line-height:1.45;color:var(--grey-text)}
.letterhead__foot strong{color:var(--blue);font-weight:500;display:block}
/* envelopes */
.envelope-back{overflow:hidden}
.envelope-back__flap{position:absolute;left:0;top:0;right:0;background:var(--black);border-radius:0 0 18px 18px;display:flex;align-items:center;justify-content:center}
.envelope-back__flap .wordmark{font-size:18px}
.envelope-back__flap .wordmark__square{width:7px;height:7px}
.envelope--dl-back{left:520px;top:430px;width:560px;height:260px}
.envelope--dl-back .envelope-back__flap{height:90px}
.envelope--dl-back-2{left:470px;top:120px;width:620px;height:290px}
.envelope--dl-back-2 .envelope-back__flap{height:100px}
.envelope--dl-front{left:110px;top:380px;width:620px;height:290px;padding:34px 40px}
.envelope--dl-front .wordmark{font-size:24px}
.envelope--dl-front .wordmark__square{width:9px;height:9px}
.envelope__return{margin-top:24px;font-size:9px;line-height:1.45;color:var(--grey-text)}
.envelope__return strong{color:var(--blue);font-weight:500;display:block}
.envelope--large{left:270px;top:150px;width:420px;height:620px}
.envelope--large .envelope-back__flap{height:90px;border-radius:0 0 10px 10px}
</style>
</head>
<body>

<section class="stage stage--cards">
  <div class="piece card card--front">
    <span class="wordmark"><span class="wordmark__square"></span>Vale 8</span>
    <span class="card__divider"></span>
    <div class="card__details">
      <p class="card__name">Marcus Elling</p>
      <p class="card__role">Managing Director</p>
      <ul class="contact">
        <li><svg viewBox="0 0 10 10"><path d="M5 0a3.5 3.5 0 0 0-3.5 3.5C1.5 6 5 10 5 10s3.5-4 3.5-6.5A3.5 3.5 0 0 0 5 0zm0 5a1.5 1.5 0 1 1 0-3 1.5 1.5 0 0 1 0 3z"/></svg>14 Birchwood Lane,<br>Atlanta, GA 30309</li>
        <li><svg viewBox="0 0 10 10"><path d="M2 0l2 2.5-1.2 1.3a6 6 0 0 0 3.4 3.4L7.5 6 10 8 8.6 9.7C4.5 9.7.3 5.5.3 1.4z"/></svg>+1 404 555 0182</li>
        <li><svg viewBox="0 0 10 10"><path d="M0 1.5h10v7H0zm1 1v.3l4 2.6 4-2.6v-.3z"/></svg>info@valeeight.com</li>
        <li><svg viewBox="0 0 10 10"><circle cx="5" cy="5" r="4.3" fill="none" stroke="#1c1c1e" stroke-width="1.1"/><path d="M.7 5h8.6M5 .7c-2.4 2.6-2.4 6 0 8.6M5 .7c2.4 2.6 2.4 6 0 8.6" fill="none" stroke="#1c1c1e" stroke-width=".9"/></svg>www.valeeight.com</li>
      </ul>
    </div>
  </div>
  <div class="piece card card--back">
    <span class="wordmark wordmark--light"><span class="wordmark__square"></span>Vale 8</span>
  </div>
</section>

<section class="stage stage--letter">
  <div class="piece letterhead letterhead--small">
    <div class="letterhead__head">
      <span class="wordmark"><span class="wordmark__square"></span>Vale 8</span>
      <div class="letterhead__firm">
        <strong>Vale 8 CPAs and Tax Advisors</strong>
        14 Birchwood Lane,<br>Atlanta, GA 30309
        <ul class="letterhead__contact">
          <li>+1 404 555 0182</li>
          <li>info@valeeight.com</li>
          <li>www.valeeight.com</li>
        </ul>
      </div>
    </div>
    <div class="letterhead__body">
      <p>Dear client,</p>
      <p>Thank you for choosing our firm to guide your investment and tax planning this year. We review every return with care and keep your goals in clear view.</p>
      <p>Our team will contact you soon to arrange a short meeting and to collect the documents needed for the coming filing season.</p>
      <p>Please reach out with any questions at all.</p>
      <p>Yours Sincerely,</p>
    </div>
  </div>
  <div class="piece envelope-back envelope--dl-back">
    <div class="envelope-back__flap">
      <span class="wordmark wordmark--light"><span class="wordmark__square"></span>Vale 8</span>
    </div>
  </div>
</section>

<section class="stage stage--envelopes">
  <div class="piece envelope-back envelope--dl-back-2">
    <div class="envelope-back__flap">
      <span class="wordmark wordmark--light"><span class="wordmark__square"></span>Vale 8</span>
    </div>
  </div>
  <div class="piece envelope--dl-front">
    <span class="wordmark"><span class="wordmark__square"></span>Vale 8</span>
    <p class="envelope__return"><strong>Vale 8 CPAs and Tax Advisors</strong>14 Birchwood Lane,<br>Atlanta, GA 30309</p>
  </div>
</section>

<section class="stage stage--large">
  <div class="piece envelope-back envelope--large">
    <div class="envelope-back__flap"></div>
  </div>
  <div class="piece letterhead letterhead--tall">
    <span class="wordmark"><span class="wordmark__square"></span>Vale 8</span>
    <p class="letterhead__foot"><strong>Vale 8 CPAs and Tax Advisors</strong>14 Birchwood Lane,<br>Atlanta, GA 30309</p>
  </div>
</section>

</body>
</html>
```